Merchandise Design for new dog product company

We are looking for merchandise designs for several items for our new dog product company. We have a logo design and would like to take design cues from the logo to apply to all of the items. Our company's products focus on giant dog breeds.

Giant breeds have presence and star power. They get noticed immediately. They are often initially intimidating until people get to know the dog and then discover they are fun-loving and good-natured. Huge Hound Goods Company (HHGCO) wants to represent this in its logo and its brand identity. HHGCO should have “swagger” with some sharp and tongue-in-cheek humor. It should be instantly recognizable from a distance and have an energy that people would be proud to represent.
The logo will appear on packaging (printed), on products (either printed and/or embroidered), and on human and canine clothing (either printed and/or embroidered).
All of the products will be “Huge Hound _____”. This is part of the fun/whimsy of the brand and will make people want to buy products for themselves or for others as gifts.
The founders have two very large Mastiffs, Rufus and Marlow. All of the marketing to consumers should feel like it is coming from Rufus and Marlow as the mascots.
Every product should ship in a box that is labeled “Huge Hound Box” and say something like “There is a Huge Hound Surprise inside!”. We want to include an oversized thank-you card (a Huge Hound Card!) that thanks each purchaser on behalf of Rufus and Marlow.

We are looking for a design for a leash, water bowl, blanket, bandana, patch for a dog harness and a thank you card.

```html
<!DOCTYPE html>
<html lang="en">
<head>
<meta charset="utf-8">
<title>Huge Hound Blanket</title>
<link rel="stylesheet" href="https://fonts.googleapis.com/css2?family=Bebas+Neue&display=swap">
<style>
  :root {
    --page: #ffffff;
    --mint: #c0fcf5;
    --orange: #f56a0d;
  }
  html, body {
    margin: 0;
    padding: 0;
    width: 1200px;
    height: 1111px;
    overflow: hidden;
    background: var(--page);
  }
  .canvas {
    position: relative;
    width: 1200px;
    height: 1111px;
    font-family: "Bebas Neue", sans-serif;
  }
  .blanket {
    position: absolute;
    left: 120px;
    top: 40px;
    width: 965px;
    height: 1016px;
    background: var(--mint);
  }
  .border-row {
    position: absolute;
    width: 710px;
    height: 36px;
    display: flex;
    justify-content: space-between;
    align-items: center;
    font-size: 28px;
    line-height: 36px;
    letter-spacing: 1px;
    white-space: nowrap;
    color: var(--orange);
  }
  .border-row--top    { left: 245px;  top: 102px; transform: rotate(180deg); }
  .border-row--bottom { left: 245px;  top: 958px; }
  .border-row--left   { left: -165px; top: 527px; transform: rotate(90deg); }
  .border-row--right  { left: 662px;  top: 527px; transform: rotate(-90deg); }

  .corner-name {
    position: absolute;
    width: 110px;
    height: 44px;
    display: flex;
    align-items: center;
    justify-content: center;
    font-size: 18px;
    line-height: 20px;
    text-align: center;
    color: var(--orange);
  }
  .corner-name--tl { left: 140px;  top: 98px;  transform: rotate(135deg); }
  .corner-name--tr { left: 955px;  top: 98px;  transform: rotate(-135deg); }
  .corner-name--bl { left: 140px;  top: 970px; transform: rotate(45deg); }
  .corner-name--br { left: 955px;  top: 970px; transform: rotate(-45deg); }
</style>
</head>
<body>
<div class="canvas">
  <div class="blanket"></div>

  <div class="corner-name corner-name--tl">Huge Hound<br>Goods Company</div>
  <div class="corner-name corner-name--tr">Huge Hound<br>Goods Company</div>
  <div class="corner-name corner-name--bl">Huge Hound<br>Goods Company</div>
  <div class="corner-name corner-name--br">Huge Hound<br>Goods Company</div>

  <div class="border-row border-row--top">
    <span>HUGE HOUND BLANKET</span>
    <span>HUGE HOUND BLANKET</span>
    <span>HUGE HOUND BLANKET</span>
  </div>
  <div class="border-row border-row--bottom">
    <span>HUGE HOUND BLANKET</span>
    <span>HUGE HOUND BLANKET</span>
    <span>HUGE HOUND BLANKET</span>
  </div>
  <div class="border-row border-row--left">
    <span>HUGE HOUND BLANKET</span>
    <span>HUGE HOUND BLANKET</span>
    <span>HUGE HOUND BLANKET</span>
  </div>
  <div class="border-row border-row--right">
    <span>HUGE HOUND BLANKET</span>
    <span>HUGE HOUND BLANKET</span>
    <span>HUGE HOUND BLANKET</span>
  </div>
</div>
</body>
</html>
```